Building company buisness cards

We are looking for a sharp modern new look for our business cards.
We are a New Zealand based company that specialises in house and land packages.
We have attached a photo of the current logo and would like to see if it can be improved somehow if needed.
We are open to any colours but we have chosen green at this stage.
Feel free to change the font and make the logo smarter looking.
Play with the colours and see what looks best.

We want a card that looks so good know one will want to throw it away!

Target Market(s)

Home buyers

Industry/Entity Type

Building

Contact Information for Business Card

Derek Tolvane
0217394062
dtolvane@quillmarkhomesteads.co.nz
quillmarkhomesteads.co.nz

Font styles to use
Serif
Sans Serif

Colors

Designer to choose colors to be used in the design.

Requirements
Must have
• Logo and company name on one side, details on the other side
Nice to have
• Color codes for the original green are HEX #4a8028, RGB(74,128,40), CMYK(42,0,69,50)
• Round corners, Raised and/or spot UV

```html
<!DOCTYPE html>
<html lang="en">
<head>
<meta charset="utf-8">
<title>Quillmark Homesteads – Business Cards</title>
<link rel="stylesheet" href="https://fonts.googleapis.com/css2?family=Open+Sans:wght@400;600&display=swap">
<style>
  :root {
    --brand-green: #4a8028;
    --card-white: #ffffff;
    --backdrop: #e9e8e6;
    --rule-grey: #c9c9c9;
    --text-dark: #3a3a3a;
  }
  html, body {
    margin: 0;
    padding: 0;
    width: 1200px;
    height: 844px;
    overflow: hidden;
    background: var(--backdrop);
    font-family: "Open Sans", Arial, sans-serif;
  }
  .sheet {
    position: relative;
    width: 1200px;
    height: 844px;
  }
  .card {
    position: absolute;
    top: 278px;
    width: 520px;
    height: 289px;
    background: var(--card-white);
    border-radius: 10px;
    box-shadow: 0 6px 18px rgba(0,0,0,0.12);
    overflow: hidden;
  }
  .card--details { left: 60px; }
  .card--brand { left: 620px; }

  .brand-block {
    position: absolute;
    display: flex;
    flex-direction: column;
    align-items: center;
  }
  .brand-name {
    display: flex;
    align-items: center;
    color: var(--brand-green);
    font-weight: 600;
    white-space: nowrap;
    line-height: 1;
  }
  .brand-square {
    flex: none;
    background: var(--brand-green);
  }
  .brand-rule {
    display: block;
    height: 1px;
    background: var(--rule-grey);
  }

  .card--details .brand-block { right: 36px; top: 80px; }
  .card--details .brand-name { font-size: 22px; gap: 10px; }
  .card--details .brand-square { width: 24px; height: 24px; }
  .card--details .brand-rule { width: 54px; margin-top: 16px; }

  .card--brand .brand-block { left: 50%; top: 112px; transform: translateX(-50%); }
  .card--brand .brand-name { font-size: 30px; gap: 14px; }
  .card--brand .brand-square { width: 34px; height: 34px; }
  .card--brand .brand-rule { width: 60px; margin-top: 20px; }

  .holder-name {
    position: absolute;
    left: 34px;
    top: 150px;
    margin: 0;
    color: var(--brand-green);
    font-size: 18px;
    font-weight: 600;
    letter-spacing: 0.2px;
    text-transform: uppercase;
  }
  .contact-list {
    position: absolute;
    left: 34px;
    top: 190px;
    margin: 0;
    padding: 0;
    list-style: none;
  }
  .contact-list li {
    display: flex;
    align-items: center;
    gap: 8px;
    height: 22px;
    color: var(--text-dark);
    font-size: 15px;
  }
  .contact-icon {
    width: 12px;
    height: 12px;
    fill: var(--brand-green);
    flex: none;
  }
</style>
</head>
<body>
<main class="sheet">

  <section class="card card--details" aria-label="Business card front with contact details">
    <div class="brand-block">
      <div class="brand-name"><span class="brand-square" aria-hidden="true"></span><span>Quillmark Homesteads</span></div>
      <span class="brand-rule"></span>
    </div>

    <h1 class="holder-name">Derek Tolvane</h1>
    <ul class="contact-list">
      <li>
        <svg class="contact-icon" viewBox="0 0 12 12" aria-hidden="true"><path d="M2.5 0.8 4.3 3 3.4 4.4c.7 1.6 2.1 3 3.7 3.7l1.4-.9 2.2 1.8-.9 1.9C5.6 10.8 1.1 6.3 0.6 2.4z"/></svg>
        <span>0217394062</span>
      </li>
      <li>
        <svg class="contact-icon" viewBox="0 0 12 12" aria-hidden="true"><path d="M0 2.5h12v7H0z M0.8 3.1 6 6.6l5.2-3.5" stroke="#fff" stroke-width="0.9"/></svg>
        <span>dtolvane@quillmarkhomesteads.co.nz</span>
      </li>
      <li>
        <svg class="contact-icon" viewBox="0 0 12 12" aria-hidden="true"><circle cx="6" cy="6" r="5.6"/><path d="M0.6 6h10.8M6 0.5c-2 2-2 9 0 11M6 0.5c2 2 2 9 0 11" stroke="#fff" stroke-width="0.8" fill="none"/></svg>
        <span>www.quillmarkhomesteads.co.nz</span>
      </li>
    </ul>
  </section>

  <section class="card card--brand" aria-label="Business card back with company name">
    <div class="brand-block">
      <div class="brand-name"><span class="brand-square" aria-hidden="true"></span><span>Quillmark Homesteads</span></div>
      <span class="brand-rule"></span>
    </div>
  </section>

</main>
</body>
</html>
```